We would like to design a logo, letter head, and business card.  

We have beauty colleges in the Kansas City Missouri USA area that have been around for 55 years.  We teach hair, skin and nail tech programs to students. Most of our students are female between the age of 18-30. 

• I appologize for failing to provide details on our addresses. We have 3 locations all with the same phone number.

Hall of Marwickton 3140 NE County Rd 9 Cedar Falls MO 64087

Hall of Marwickton 4630 Pellham Kansas City MO 64110

Hall of Marwickton 10870 Green Hollow Blvd Fairmont Mo 64152

Phone: (816) 555-0147

• Dennis Marwickton

President

3140 NE County Rd 9

Cedar Falls MO 64087

(816) 555-0147

dennis@zq-tress.com

Target Market(s)

18-30 Years Old

Industry/Entity Type

Business

Logo Text

Hall of Marwickton Beauty College

Requirements
Must have
• Hall of Marwickton Beauty College

```html
<!DOCTYPE html>
<html lang="en">
<head>
<meta charset="utf-8">
<title>Hall of Marwickton Beauty College — Identity</title>
<link rel="stylesheet" href="https://fonts.googleapis.com/css2?family=Crimson+Text&family=Arimo&display=swap">
<style>
  :root {
    --brand-blue: #23208c;
    --paper: #ffffff;
    --frame: #5a57b0;
    --ink-light: #ffffff;
    --serif: "Crimson Text", Georgia, serif;
    --sans: "Arimo", Arial, sans-serif;
  }
  * { box-sizing: border-box; margin: 0; padding: 0; }
  html, body { width: 825px; height: 1200px; overflow: hidden; background: var(--paper); }
  .canvas { position: relative; width: 825px; height: 1200px; background: var(--paper); }

  .wordmark { color: var(--brand-blue); font-family: var(--serif); font-weight: 400; text-align: center; line-height: 1.05; }
  .wordmark__dot { display: block; margin: 0 auto; border-radius: 50%; background: var(--brand-blue); }

  .brand-mark { position: absolute; left: 40px; top: 40px; width: 260px; }
  .brand-mark .wordmark__dot { width: 90px; height: 90px; margin-bottom: 36px; }
  .brand-mark .wordmark { font-size: 33px; }

  .letterhead { position: absolute; left: 44px; top: 316px; width: 682px; height: 883px; border: 1px solid var(--frame); background: var(--paper); }
  .letterhead__logo { position: absolute; left: 0; right: 0; top: 36px; }
  .letterhead__logo .wordmark__dot { width: 52px; height: 52px; margin-bottom: 16px; }
  .letterhead__logo .wordmark { font-size: 19px; }
  .letterhead__name { position: absolute; left: 0; right: 0; bottom: 70px; text-align: center; font-family: var(--serif); font-size: 15px; color: var(--brand-blue); }
  .letterhead__footer { position: absolute; left: 0; right: 0; bottom: 0; height: 62px; background: var(--brand-blue); color: var(--ink-light); font-family: var(--sans); font-size: 10px; line-height: 1.3; text-align: center; padding-top: 6px; }

  .card { position: absolute; left: 525px; width: 283px; height: 162px; border: 1px solid var(--brand-blue); }
  .card--back { top: 525px; background: var(--brand-blue); }
  .card--back .wordmark { position: absolute; left: 0; right: 0; top: 50px; color: var(--ink-light); font-size: 13px; }
  .card--back .wordmark__dot { width: 34px; height: 34px; background: var(--ink-light); margin-bottom: 10px; }

  .card--front { top: 712px; background: var(--paper); }
  .card__person { text-align: center; padding-top: 14px; color: var(--brand-blue); }
  .card__name { font-family: var(--serif); font-size: 11.5px; }
  .card__title { font-family: var(--sans); font-size: 8px; margin-bottom: 7px; }
  .card__detail { font-family: var(--sans); font-size: 8.5px; line-height: 1.2; }
  .card__brand { text-align: center; font-family: var(--serif); font-size: 11px; color: var(--brand-blue); margin-top: 8px; }
  .card__footer { position: absolute; left: 0; right: 0; bottom: 0; height: 48px; background: var(--brand-blue); color: var(--ink-light); font-family: var(--sans); font-size: 8.5px; line-height: 1.3; text-align: center; padding-top: 6px; }
</style>
</head>
<body>
<main class="canvas">

  <section class="brand-mark">
    <span class="wordmark__dot"></span>
    <p class="wordmark">Hall of Marwickton<br>Beauty College</p>
  </section>

  <section class="letterhead">
    <div class="letterhead__logo">
      <span class="wordmark__dot"></span>
      <p class="wordmark">Hall of Marwickton<br>Beauty College</p>
    </div>
    <p class="letterhead__name">Hall of Marwickton</p>
    <footer class="letterhead__footer">
      3140 NE County Rd 9 Cedar Falls MO 64087<br>
      4630 Pellham Kansas City MO 64110<br>
      10870 Green Hollow Blvd Fairmont Mo 64152<br>
      t. (816) 555-0147
    </footer>
  </section>

  <section class="card card--back">
    <div class="wordmark">
      <span class="wordmark__dot"></span>
      Hall of Marwickton<br>Beauty College
    </div>
  </section>

  <section class="card card--front">
    <div class="card__person">
      <p class="card__name">Dennis Marwickton</p>
      <p class="card__title">President</p>
      <p class="card__detail">3140 NE County Rd 9 Cedar Falls MO 64087</p>
      <p class="card__detail">t. (816) 555-0147</p>
      <p class="card__detail">e. dennis@zq-tress.com</p>
    </div>
    <p class="card__brand">Hall of Marwickton</p>
    <footer class="card__footer">
      3140 NE County Rd 9 Cedar Falls MO 64087<br>
      4630 Pellham Kansas City MO 64110<br>
      10870 Green Hollow Blvd Fairmont Mo 64152
    </footer>
  </section>

</main>
</body>
</html>
```